Visit card

Industry/Entity Type

Health Care

Contact Information for Business Card

O VITALIS SYSTEMS
Odile Brevard - chef de Projet

Requirements
Must have
• 318 Gaston Lemaire Street 59710 BÉTHUNE Tel: 33 (0) 327 481 605 Mobile: 06 42 19 37 64 Web: www.quorvexsystems.example Contact: o.brevard@o-vitalissystems.example
Should not have
• Respect for color

```html
<!DOCTYPE html>
<html lang="fr">
<head>
<meta charset="utf-8">
<title>O Vitalis Systems — Carte de visite</title>
<link rel="stylesheet" href="https://fonts.googleapis.com/css2?family=Lato:ital,wght@0,400;0,700;0,900;1,400&display=swap">
<style>
  :root {
    --bg: #2b2c2e;
    --card: #ffffff;
    --card-shade: #ececec;
    --ink: #3a3a3c;
    --muted: #5c5c5e;
    --red: #e01b2b;
    --dark: #333436;
    --rule: #6d6d6f;
  }
  * { box-sizing: border-box; margin: 0; padding: 0; }
  html, body { width: 1200px; height: 900px; overflow: hidden; }
  body {
    background: var(--bg);
    font-family: "Lato", sans-serif;
    display: flex; align-items: center; justify-content: center;
  }
  .card {
    position: relative;
    width: 1000px; height: 572px;
    border-radius: 28px;
    overflow: hidden;
    background: radial-gradient(circle at 70% 30%, var(--card) 0%, var(--card) 45%, var(--card-shade) 100%);
    box-shadow: 0 20px 50px rgba(0,0,0,.45);
  }
  .brand {
    position: absolute; left: 56px; top: 44px;
    display: flex; align-items: center; gap: 18px;
  }
  .brand-dot {
    width: 62px; height: 62px; border-radius: 50%;
    background: var(--dark);
  }
  .brand-name {
    font-weight: 900; font-size: 34px; letter-spacing: 1px;
    color: var(--red);
  }
  .divider {
    position: absolute; left: 40px; right: 40px; top: 250px;
    height: 2px; background: var(--rule);
  }
  .contacts {
    position: absolute; left: 56px; top: 282px;
    list-style: none;
    font-size: 21px; color: var(--ink);
    line-height: 36px;
  }
  .contacts li { display: flex; align-items: center; gap: 14px; }
  .contacts svg { width: 15px; height: 15px; flex: none; }
  .person {
    position: absolute; right: 56px; top: 140px; text-align: right;
  }
  .person-name {
    font-size: 38px; font-weight: 400; letter-spacing: 1px;
    color: var(--red); text-transform: uppercase;
  }
  .person-role {
    font-size: 22px; font-style: italic; color: var(--ink);
    margin-top: 4px;
  }
  .address {
    position: absolute; right: 56px; top: 392px; text-align: right;
    font-size: 23px; color: var(--ink); line-height: 36px;
  }
  .footer-band { position: absolute; left: 0; bottom: 0; width: 1000px; height: 80px; }
</style>
</head>
<body>
  <main class="card">
    <div class="brand">
      <span class="brand-dot"></span>
      <span class="brand-name">O VITALIS SYSTEMS</span>
    </div>

    <div class="person">
      <p class="person-name">Odile Brevard</p>
      <p class="person-role">Chef de Projet</p>
    </div>

    <div class="divider"></div>

    <ul class="contacts">
      <li>
        <svg viewBox="0 0 16 16"><path d="M4 1l3 3-2 2c1 2 3 4 5 5l2-2 3 3-2 3C7 15 1 9 1 3z" fill="#e01b2b"/></svg>
        +33 (0) 327 481 605
      </li>
      <li>
        <svg viewBox="0 0 16 16"><rect x="4" y="1" width="8" height="14" rx="1.5" fill="none" stroke="#e01b2b" stroke-width="2"/></svg>
        06 42 19 37 64
      </li>
      <li>
        <svg viewBox="0 0 16 16"><circle cx="8" cy="8" r="6.5" fill="none" stroke="#e01b2b" stroke-width="1.6"/><path d="M1.5 8h13M8 1.5c-3 3-3 10 0 13M8 1.5c3 3 3 10 0 13" fill="none" stroke="#e01b2b" stroke-width="1.2"/></svg>
        www.quorvexsystems.example
      </li>
      <li>
        <svg viewBox="0 0 16 16"><rect x="1" y="3" width="14" height="10" fill="none" stroke="#e01b2b" stroke-width="1.6"/><path d="M1 3l7 6 7-6" fill="none" stroke="#e01b2b" stroke-width="1.6"/></svg>
        o.brevard@o-vitalissystems.example
      </li>
    </ul>

    <div class="address">
      <p>318 Rue Gaston Lemaire</p>
      <p>59710 BÉTHUNE</p>
    </div>

    <svg class="footer-band" viewBox="0 0 1000 80" preserveAspectRatio="none" aria-hidden="true">
      <path d="M0 14 L400 38 L400 44 L0 22 Z" fill="var(--red)"/>
      <path d="M0 30 L440 50 C470 52 480 62 500 70 C515 76 530 78 560 80 L0 80 Z" fill="var(--dark)"/>
    </svg>
  </main>
</body>
</html>
```